Tolvar Air and Electrical Website

Simple and easy to use website for a Electrical and Air Conditioning contracting business.Use stock photosOnline contact portallogo still to be supplied

Target Market(s)

Mums and Dads who want a local contractor

Coding

Coded - Design and coding required

Number of Pages Required

2 page

Font styles to use
Sans Serif

Colors
f04a50
3276b5
33a6d7

Requirements
Must have
• Simple and easy to use
• Ph number
• 4 web address; linked to page
• 0417385926
• tolvar.com.au
• tolvarelectrical.com.au
• tolvarairandelectrical.com.au
• tolvarair.com.au
Nice to have
• Split System Air Con Picture
• Electrical Pictures

```html
<!DOCTYPE html>
<html lang="en">
<head>
<meta charset="utf-8">
<title>Tolvar Air and Electrical</title>
<link rel="stylesheet" href="https://fonts.googleapis.com/css2?family=Exo+2:wght@300;400;500;600;800&family=Didact+Gothic&display=swap">
<style>
:root{
  --red:#f04a50;
  --red-deep:#d9343b;
  --blue:#3276b5;
  --sky:#33a6d7;
  --ink:#1e1e1e;
  --text:#2b2b2b;
  --white:#ffffff;
  --dark:#2a2c30;
}
*{margin:0;padding:0;box-sizing:border-box}
html,body{width:1200px;height:3995px;overflow:hidden;background:var(--white)}
body{position:relative;font-family:"Didact Gothic",sans-serif;color:var(--text)}
.shapes{position:absolute;left:0;top:0}
.abs{position:absolute}
a{color:inherit;text-decoration:none}

/* header */
.logo{left:88px;top:46px;font-family:"Exo 2",sans-serif;font-weight:500;font-size:50px;letter-spacing:3px;color:var(--red);line-height:1}
.contact-item{display:flex;align-items:center;gap:12px;font-size:15px;line-height:1.35;color:var(--ink)}
.contact-item .label{color:var(--sky);font-size:14px}
.search{left:857px;top:31px;width:253px;height:44px;border:1px solid #d6d6d6;border-radius:22px;display:flex;align-items:center;justify-content:space-between;padding:0 6px 0 18px;font-size:14px;color:#888}
.search .go{width:32px;height:32px;border-radius:50%;background:var(--red);display:flex;align-items:center;justify-content:center}
.nav{top:106px;left:437px;width:673px;display:flex;justify-content:space-between;font-size:16.5px;font-weight:600;color:var(--ink);font-family:"Exo 2",sans-serif}

/* shared */
.btn{display:inline-flex;align-items:center;justify-content:center;gap:8px;height:50px;width:182px;border-radius:25px;color:var(--white);font-size:16px;font-family:"Exo 2",sans-serif;font-weight:500;box-shadow:0 3px 6px rgba(0,0,0,.18)}
.btn.red{background:var(--red)}
.btn.sky{background:var(--sky)}
.btn .arrow{width:15px;height:15px;border-radius:50%;background:var(--white);display:inline-flex;align-items:center;justify-content:center}
.copy{font-size:14px;line-height:31px;text-align:justify;text-align-last:left}
.copy.right{text-align-last:right}
.white{color:var(--white)}

/* hero */
.hero-title{left:600px;top:292px;font-family:"Exo 2",sans-serif;font-size:52px;font-weight:500;color:var(--sky)}
.hero-text{left:600px;top:360px;width:510px;font-size:14.5px;line-height:36px;color:var(--white);text-align:justify;text-align-last:left}
.hero-btn{left:600px;top:482px}

/* about */
.about-kicker{left:88px;top:998px;font-family:"Exo 2",sans-serif;font-size:22px;color:var(--ink)}
.about-title{left:88px;top:1030px;font-family:"Exo 2",sans-serif;font-weight:300;font-size:41px;color:var(--sky)}
.about-text{left:88px;top:1096px;width:512px;font-size:15.5px;line-height:36px;text-align:justify;text-align-last:left;color:var(--text)}
.about-btn{left:88px;top:1378px}

/* services */
.svc-title{font-family:"Exo 2",sans-serif;font-weight:300;font-size:37px;line-height:50px;color:var(--white)}
.svc-main{right:90px;top:1458px;text-align:right}
.svc-main-text{left:600px;top:1519px;width:510px}
.svc-main-btn{left:928px;top:1634px}
.svc-air{left:88px;top:1758px}
.svc-air-text{left:88px;top:1869px;width:512px}
.svc-air-btn{left:88px;top:1985px}
.svc-elec{right:90px;top:2140px;text-align:right}
.svc-elec-text{left:600px;top:2245px;width:510px}
.svc-elec-btn{left:928px;top:2359px}
.svc-help{left:88px;top:2502px;font-size:40px}
.svc-help-text{left:88px;top:2565px;width:583px;font-size:15px}
.svc-help-btn{left:88px;top:2681px}

/* testimonials */
.slider-arrows{left:1049px;top:2892px;display:flex;gap:4px}
.slider-arrows span{width:22px;height:22px;border-radius:50%;background:var(--ink);display:flex;align-items:center;justify-content:center}
.testi-title{left:0;top:2915px;width:1200px;text-align:center;font-family:"Exo 2",sans-serif;font-weight:500;font-size:41px;color:var(--sky)}
.quote{left:0;width:1200px;text-align:center;font-family:"Exo 2",sans-serif;font-weight:800;font-size:150px;line-height:1;height:60px;color:var(--red)}
.quote.open{top:2982px}
.quote.close{top:3132px;transform:scaleX(-1)}
.testi-text{left:144px;top:3054px;width:912px;text-align:center;font-size:15.5px;line-height:36px;color:var(--ink)}
.dots{left:88px;top:3221px;display:flex;gap:5px}
.dots span{width:15px;height:15px;border-radius:50%;background:var(--ink)}
.dots span.on{background:var(--white);border:4px solid var(--ink)}

/* footer */
.foot-item{top:3636px;width:260px;text-align:center;color:var(--white);font-size:17px;line-height:28px}
.diamond{width:66px;height:66px;margin:0 auto 20px;background:var(--red);transform:rotate(45deg);border-radius:8px;display:flex;align-items:center;justify-content:center}
.diamond svg{transform:rotate(-45deg)}
.foot-links{left:0;top:3820px;width:1200px;text-align:center;color:var(--white);font-size:17px}
.foot-links span{margin:0 9px}
.foot-sites{left:0;top:3852px;width:1200px;text-align:center;color:var(--white);font-size:14px}
.foot-sites span{margin:0 8px}
.foot-copy{left:0;top:3886px;width:1200px;text-align:center;color:var(--white);font-size:15px}
.socials{left:530px;top:3936px;display:flex;gap:6px}
.socials span{width:31px;height:31px;border-radius:50%;border:2px solid var(--white)}
</style>
</head>
<body>

<svg class="shapes" width="1200" height="3995" viewBox="0 0 1200 3995">
  <defs>
    <linearGradient id="heroPhoto" x1="0" y1="0" x2="1" y2="1">
      <stop offset="0" stop-color="#3c4d6b"/>
      <stop offset=".45" stop-color="#1f2636"/>
      <stop offset="1" stop-color="#2e3a52"/>
    </linearGradient>
    <linearGradient id="hexPhoto" x1="0" y1="0" x2="1" y2="1">
      <stop offset="0" stop-color="#8a5f3b"/>
      <stop offset=".6" stop-color="#6f7a6e"/>
      <stop offset="1" stop-color="#9fb3c4"/>
    </linearGradient>
    <linearGradient id="redPhoto" x1="0" y1="0" x2="1" y2="1">
      <stop offset="0" stop-color="#f04a50"/>
      <stop offset="1" stop-color="#d5313a"/>
    </linearGradient>
    <linearGradient id="bluePhoto" x1="0" y1="0" x2="1" y2="1">
      <stop offset="0" stop-color="#2f8cc6"/>
      <stop offset="1" stop-color="#2a6fae"/>
    </linearGradient>
    <linearGradient id="footPhoto" x1="0" y1="0" x2="1" y2="1">
      <stop offset="0" stop-color="#3a3c40"/>
      <stop offset="1" stop-color="#1e1f22"/>
    </linearGradient>
  </defs>

  <polygon role="img" aria-label="Photo of an electrician in a hard hat working with a sparking power cable" fill="url(#heroPhoto)" points="0,153 1200,153 1200,535 299,860 0,721"/>
  <polygon fill="var(--red)" points="0,716 299,850 1200,528 1200,545 299,870 0,730"/>

  <polygon fill="none" stroke="var(--red)" stroke-width="2.5" points="598,977 722,756 986,756 1110,977 986,1197 722,1197"/>
  <polygon role="img" aria-label="Photo of an air conditioning technician's tool bag and pressure gauges" fill="url(#hexPhoto)" points="612,977 730,769 978,769 1096,977 978,1185 730,1185"/>

  <polygon role="img" aria-label="Red tinted photo of electricians working on switchboards" fill="url(#redPhoto)" points="211,1545 1008,1256 1200,1294 1200,2716 0,2147"/>
  <polygon role="img" aria-label="Blue tinted photo of an air conditioning technician servicing a unit" fill="url(#bluePhoto)" points="0,1449 992,1945 0,2155"/>
  <polygon role="img" aria-label="Blue tinted photo of an electrician carrying a cable coil" fill="url(#bluePhoto)" points="0,2147 992,2426 194,2911 0,2834"/>

  <polygon role="img" aria-label="Dark photo of a tradesman beside a work vehicle" fill="url(#footPhoto)" points="0,3619 900,3283 1200,3426 1200,3995 0,3995"/>
  <polyline fill="none" stroke="var(--red)" stroke-width="5" points="0,3619 900,3283 1200,3426"/>
</svg>

<!-- header -->
<div class="abs logo">TOLVAR</div>
<div class="abs contact-item" style="left:436px;top:31px">
  <svg width="40" height="40" viewBox="0 0 40 40"><circle cx="20" cy="20" r="18" fill="none" stroke="var(--red)" stroke-width="2.5"/><path d="M14 11c-2 1-3 3-2 6 2 6 6 10 12 12 3 1 5 0 6-2l-4-4-3 2c-3-1-6-4-7-7l2-3z" fill="var(--red)"/></svg>
  <div><div class="label">CALL US:</div>0417385926</div>
</div>
<div class="abs contact-item" style="left:626px;top:31px">
  <svg width="44" height="40" viewBox="0 0 44 40"><rect x="3" y="12" width="38" height="26" fill="none" stroke="var(--red)" stroke-width="2.5"/><path d="M3 12l19 14 19-14" fill="none" stroke="var(--red)" stroke-width="2.5"/><rect x="12" y="3" width="20" height="15" fill="#fff" stroke="var(--red)" stroke-width="2"/><path d="M15 8h14M15 12h10" stroke="var(--red)" stroke-width="2"/></svg>
  <div><div class="label">SUPPORT MAIL US</div>info@tolvar.com.au</div>
</div>
<div class="abs search">Search
  <span class="go"><svg width="14" height="14" viewBox="0 0 14 14"><circle cx="6" cy="6" r="4" fill="none" stroke="#fff" stroke-width="2"/><path d="M9 9l3.5 3.5" stroke="#fff" stroke-width="2"/></svg></span>
</div>
<nav class="abs nav"><span>HOME</span><span>ABOUT US</span><span>OUR SERVICES</span><span>TESTIMONIALS</span><span>CONTACT US</span></nav>

<!-- hero -->
<h1 class="abs hero-title">Tolvar</h1>
<p class="abs hero-text">Lorem ipsum dolor sit amet, consectetur adipiscing elit, sed do eiusmod tempor incididunt ut labore et dolore magna aliqua. Quis ipsum suspendisse ultrices gravida.</p>
<a class="abs btn red hero-btn">READ MORE <span class="arrow"><svg width="8" height="8" viewBox="0 0 8 8"><path d="M2 1l3 3-3 3" fill="none" stroke="var(--red)" stroke-width="2"/></svg></span></a>

<!-- about -->
<div class="abs about-kicker">About us</div>
<h2 class="abs about-title">Welcome to Tolvar</h2>
<p class="abs about-text">Lorem ipsum dolor sit amet, consectetur adipiscing elit, sed do eiusmod tempor incididunt ut labore et dolore magna aliqua. Quis ipsum suspendisse ultrices gravida. Risus commodo viverra maecenas accumsan lacus vel facilisis. Lorem ipsum dolor sit amet, consectetur adipiscing elit, sed do eiusmod tempor incididunt ut labore et dolore magna aliqua. sed do eiusmod tempor incididunt ut labore et dolore magna aliqua.</p>
<a class="abs btn red about-btn">READ MORE <span class="arrow"><svg width="8" height="8" viewBox="0 0 8 8"><path d="M2 1l3 3-3 3" fill="none" stroke="var(--red)" stroke-width="2"/></svg></span></a>

<!-- services -->
<h2 class="abs svc-title svc-main">Our Services</h2>
<p class="abs copy right white svc-main-text">Sed ut perspiciatis unde omnis iste natus error sit voluptatem accusantium doloremque laudantium, totam rem aperiam, eaque ipsa quae ab illo inventore veritatis et quasi architecto beatae vitae dicta sunt explicabo</p>
<a class="abs btn sky svc-main-btn">READ MORE <span class="arrow"><svg width="8" height="8" viewBox="0 0 8 8"><path d="M2 1l3 3-3 3" fill="none" stroke="var(--sky)" stroke-width="2"/></svg></span></a>

<h2 class="abs svc-title svc-air">Air Conditioning<br>Contracting Business.</h2>
<p class="abs copy white svc-air-text">Sed ut perspiciatis unde omnis iste natus error sit voluptatem accusantium doloremque laudantium, totam rem aperiam, eaque ipsa quae ab illo inventore veritatis et quasi architecto beatae vitae dicta sunt explicabo</p>
<a class="abs btn red svc-air-btn">READ MORE <span class="arrow"><svg width="8" height="8" viewBox="0 0 8 8"><path d="M2 1l3 3-3 3" fill="none" stroke="var(--red)" stroke-width="2"/></svg></span></a>

<h2 class="abs svc-title svc-elec">Electrical Contracting<br>Business.</h2>
<p class="abs copy right white svc-elec-text">Sed ut perspiciatis unde omnis iste natus error sit voluptatem accusantium doloremque laudantium, totam rem aperiam, eaque ipsa quae ab illo inventore veritatis et quasi architecto beatae vitae dicta sunt explicabo</p>
<a class="abs btn sky svc-elec-btn">READ MORE <span class="arrow"><svg width="8" height="8" viewBox="0 0 8 8"><path d="M2 1l3 3-3 3" fill="none" stroke="var(--sky)" stroke-width="2"/></svg></span></a>

<h2 class="abs svc-title svc-help">Need help or Have questions ?</h2>
<p class="abs copy white svc-help-text">Sed ut perspiciatis unde omnis iste natus error sit voluptatem accusantium doloremque laudantium, totam rem aperiam, eaque ipsa quae ab illo inventore veritatis et quasi architecto beatae vitae dicta sunt explicabo.</p>
<a class="abs btn red svc-help-btn">READ MORE <span class="arrow"><svg width="8" height="8" viewBox="0 0 8 8"><path d="M2 1l3 3-3 3" fill="none" stroke="var(--red)" stroke-width="2"/></svg></span></a>

<!-- testimonials -->
<div class="abs slider-arrows">
  <span><svg width="10" height="10" viewBox="0 0 10 10"><path d="M6.5 1.5L3 5l3.5 3.5" fill="none" stroke="#fff" stroke-width="2"/></svg></span>
  <span><svg width="10" height="10" viewBox="0 0 10 10"><path d="M3.5 1.5L7 5 3.5 8.5" fill="none" stroke="#fff" stroke-width="2"/></svg></span>
</div>
<h2 class="abs testi-title">Testimonials</h2>
<div class="abs quote open">&ldquo;</div>
<p class="abs testi-text">Lorem ipsum dolor sit amet, consectetur adipiscing elit, sed do eiusmod tempor incididunt ut labore et dolore magna aliqua. Quis ipsum suspendisse ultrices gravida. Risus commodo viverra maecenas accumsan lacus vel facilisis.</p>
<div class="abs quote close">&ldquo;</div>
<div class="abs dots"><span></span><span></span><span class="on"></span><span></span><span></span></div>

<!-- footer -->
<div class="abs foot-item" style="left:234px">
  <div class="diamond"><svg width="34" height="34" viewBox="0 0 34 34"><path d="M9 5c-3 1-4 4-3 8 3 8 8 13 16 16 4 1 7 0 8-3l-5-5-4 2c-4-2-7-5-9-9l2-4z" fill="none" stroke="#fff" stroke-width="2"/></svg></div>
  Phone:<br>0417385926
</div>
<div class="abs foot-item" style="left:468px">
  <div class="diamond"><svg width="34" height="34" viewBox="0 0 34 34"><path d="M17 31s10-10 10-18a10 10 0 0 0-20 0c0 8 10 18 10 18z" fill="none" stroke="#fff" stroke-width="2"/><circle cx="17" cy="13" r="4" fill="none" stroke="#fff" stroke-width="2"/></svg></div>
  2207 Wattlebrook Rd, Kelmscott,<br>WA 6111
</div>
<div class="abs foot-item" style="left:704px">
  <div class="diamond"><svg width="34" height="34" viewBox="0 0 34 34"><rect x="4" y="8" width="26" height="18" fill="none" stroke="#fff" stroke-width="2"/><path d="M4 8l13 10 13-10" fill="none" stroke="#fff" stroke-width="2"/></svg></div>
  Email:<br>info@tolvar.com.au
</div>
<div class="abs foot-links">Home<span>|</span>About Us<span>|</span>Our Services<span>|</span>Testimonials<span>|</span>Contact Us</div>
<div class="abs foot-sites"><a href="https://tolvar.com.au">tolvar.com.au</a><span>|</span><a href="https://tolvarelectrical.com.au">tolvarelectrical.com.au</a><span>|</span><a href="https://tolvarairandelectrical.com.au">tolvarairandelectrical.com.au</a><span>|</span><a href="https://tolvarair.com.au">tolvarair.com.au</a></div>
<div class="abs foot-copy">&copy;Tolvar 2019. All rights reserved</div>
<div class="abs socials"><span></span><span></span><span></span><span></span></div>

</body>
</html>
```